Varnex Consulting Business card design.

See our website www.varnexconsulting.example which will give you a good idea of what we are about. The font is called 'Play'.

I'd like a standout business card in keeping with the themes and branding on the website

Target Market(s)

professionals. HR directors

Industry/Entity Type

Business

Contact Information for Business Card

Varnex Consulting PO Box 3172 Merrowdale NSW 2291 1300 485 193 Gavin Threlkeld Principal email: career@varnexconsulting.example ABN: 71203948865

Font styles to use
Other font styles liked:
• Play

Requirements
Must have
• Must have same design colours and branding as website.
• On back I'd prefer a list of the things we do which appears below the name at the header on the website

```html
<!DOCTYPE html>
<html lang="en">
<head>
<meta charset="utf-8">
<title>Varnex Consulting – Business Card</title>
<link href="https://fonts.googleapis.com/css2?family=Play:wght@400;700&display=swap" rel="stylesheet">
<style>
  :root {
    --navy: #1a2a3c;
    --blue: #2a93dc;
    --card: #ffffff;
    --backdrop: #ecebea;
    --text: #1f2a36;
  }
  * { margin: 0; padding: 0; box-sizing: border-box; }
  html, body {
    width: 1200px; height: 1200px; overflow: hidden;
    background: var(--backdrop);
    font-family: "Play", sans-serif;
    color: var(--text);
  }
  .canvas { position: relative; width: 1200px; height: 1200px; }
  .card {
    position: absolute;
    width: 712px; height: 417px;
    background: var(--card);
    overflow: hidden;
  }
  .card--front { left: 238px; top: 119px; }
  .card--back  { left: 230px; top: 645px; }

  .brand { position: absolute; left: 0; right: 0; text-align: center; }
  .brand__name {
    font-size: 55px; font-weight: 400; letter-spacing: 1px;
    color: var(--navy); line-height: 1; white-space: nowrap;
  }
  .brand__services {
    margin-top: 14px;
    font-size: 15px; letter-spacing: 2.2px; color: var(--blue);
    white-space: nowrap;
  }
  .brand__services .sep { color: var(--navy); margin: 0 5px; }
  .card--front .brand { top: 130px; }
  .card--back .brand { top: 66px; }
  .card--back .brand__name { font-size: 57px; }

  .web-line {
    position: absolute; left: 0; right: 0; top: 346px;
    display: flex; justify-content: center; align-items: center; gap: 12px;
    font-size: 18px; color: var(--navy);
  }
  .web-line .dash { width: 34px; height: 2px; background: var(--blue); }
  .accent { color: var(--blue); }

  .person { position: absolute; left: 41px; top: 216px; }
  .person__name { font-size: 24px; font-weight: 700; color: var(--navy); }
  .person__role { margin-top: 8px; font-size: 17px; color: var(--text); }

  .contact { position: absolute; left: 333px; top: 214px; font-size: 18px; color: var(--text); }
  .contact__row { display: flex; align-items: center; height: 27.5px; }
  .contact__row svg { width: 18px; height: 14px; margin-right: 17px; fill: var(--blue); }
  .contact__line { height: 29px; line-height: 29px; }
  .contact__line--first { margin-top: 3px; }

  .footer-band { position: absolute; left: 0; bottom: 0; width: 712px; height: 18px; }
</style>
</head>
<body>
<main class="canvas">

  <section class="card card--front" aria-label="Business card front">
    <div class="brand">
      <div class="brand__name">VARNEX CONSULTING</div>
      <div class="brand__services">Search &amp; Select<span class="sep">I</span>Career<span class="sep">I</span>Coaching<span class="sep">I</span>Leadership<span class="sep">I</span>Outplacement</div>
    </div>
    <div class="web-line">
      <span class="dash"></span>
      <span>www.<span class="accent">varnexconsulting</span>.example</span>
      <span class="dash"></span>
    </div>
  </section>

  <section class="card card--back" aria-label="Business card back">
    <div class="brand">
      <div class="brand__name">VARNEX CONSULTING</div>
      <div class="brand__services">Search &amp; Select<span class="sep">I</span>Career<span class="sep">I</span>Coaching<span class="sep">I</span>Leadership<span class="sep">I</span>Outplacement</div>
    </div>

    <div class="person">
      <div class="person__name">Gavin Threlkeld</div>
      <div class="person__role">Principal</div>
    </div>

    <div class="contact">
      <div class="contact__row">
        <svg viewBox="0 0 18 14" aria-hidden="true"><path d="M1 4 Q9 -1 17 4 L15 6 L12 4.5 L12 3 Q9 2 6 3 L6 4.5 L3 6 Z"/><path d="M4 7 L14 7 L16 13 L2 13 Z"/><circle cx="9" cy="10" r="1.6" fill="#fff"/></svg>
        <span>1300 485 193</span>
      </div>
      <div class="contact__row">
        <svg viewBox="0 0 18 14" aria-hidden="true"><circle cx="9" cy="7" r="6.5"/><g fill="none" stroke="#fff" stroke-width="1"><ellipse cx="9" cy="7" rx="2.6" ry="6.5"/><line x1="2.5" y1="7" x2="15.5" y2="7"/><line x1="3.5" y1="4" x2="14.5" y2="4"/><line x1="3.5" y1="10" x2="14.5" y2="10"/></g></svg>
        <span>www.<span class="accent">varnexconsulting</span>.example</span>
      </div>
      <div class="contact__row">
        <svg viewBox="0 0 18 14" aria-hidden="true"><rect x="1" y="1.5" width="16" height="11"/><path d="M1 1.5 L9 8 L17 1.5 M1 12.5 L7 6.5 M17 12.5 L11 6.5" fill="none" stroke="#fff" stroke-width="1.2"/></svg>
        <span>career@varnexconsulting.example</span>
      </div>
      <div class="contact__line contact__line--first" style="margin-left:-35px"><span class="accent">ABN:</span> 71203948865</div>
      <div class="contact__line" style="margin-left:-35px">PO Box 3172 Merrowdale NSW 2291</div>
    </div>

    <svg class="footer-band" viewBox="0 0 712 18" aria-hidden="true">
      <polygon points="0,0 500,0 464,18 0,18" fill="var(--navy)"/>
      <polygon points="508,0 712,0 712,18 472,18" fill="var(--blue)"/>
    </svg>
  </section>

</main>
</body>
</html>
```